web page design with coding

We are a start up insurance agency who needs to design a full functional web page. we recently did a postcard design though drawkettle I will upload the final project for you to see the color scheme/font we would like to continue to use. I also have a rough draft of verbage I would like our website to have. I will upload that as well.

Reason: I am sorry but the person who will make the final decision on the website is out of the country at the moment and will make the final decision when he returns.

Industry/Entity Type

Insurance

Coding

Coded - Design and coding required

```html
<!DOCTYPE html>
<html lang="en">
<head>
<meta charset="utf-8">
<title>Harborline Insurance Group</title>
<link href="https://fonts.googleapis.com/css2?family=EB+Garamond:ital,wght@0,500;1,500;1,600&family=Open+Sans:wght@400;600;700&display=swap" rel="stylesheet">
<style>
:root{
  --navy:#173b72;
  --navy-deep:#12305f;
  --green:#2a7d3c;
  --green-text:#2b7a3a;
  --ink:#333;
  --muted:#555;
  --line:#e2e2e2;
  --grey-bg:#f1f1f1;
  --white:#fff;
}
*{box-sizing:border-box;margin:0;padding:0}
html,body{width:1200px;height:2290px;overflow:hidden}
body{position:relative;font-family:"Open Sans",Arial,sans-serif;color:var(--ink);background:var(--white)}
.abs{position:absolute}
.topline{left:0;top:0;width:1200px;height:4px;background:linear-gradient(90deg,var(--green),var(--navy))}

/* header */
.brand{left:162px;top:40px;font-family:"EB Garamond",Georgia,serif;font-weight:500;color:var(--navy);font-size:28px;line-height:32px;display:flex;align-items:center;gap:10px;white-space:nowrap}
.brand-mark{width:13px;height:13px;background:var(--navy)}
.top-contact{top:25px;font-size:12.5px;color:var(--muted);display:flex;align-items:center;gap:10px;white-space:nowrap}
.icon-ring{width:26px;height:26px;border:2px solid var(--green);border-radius:50%;display:flex;align-items:center;justify-content:center}
.nav-item{top:84px;font-size:12.5px;font-weight:600;color:#333;letter-spacing:.2px;white-space:nowrap}
.nav-item.active{color:var(--navy)}
.search{left:1004px;top:73px;width:38px;height:38px;border-radius:50%;background:var(--navy);display:flex;align-items:center;justify-content:center}

/* hero */
.hero{left:0;top:128px;width:1200px;height:507px;background:linear-gradient(100deg,#8a8f84 0%,#b7b3a8 35%,#9fb08a 55%,#c8c6bc 75%,#7f9a62 100%)}
.hero-title{right:160px;top:318px;text-align:right;color:var(--white);font-family:"EB Garamond",Georgia,serif;font-style:italic;font-weight:600;font-size:56px;line-height:54px}
.btn-quote{left:862px;top:458px;width:176px;height:41px;background:var(--navy);color:var(--white);font-size:14px;font-weight:700;display:flex;align-items:center;justify-content:center;gap:10px}
.hero-arrow{top:368px}

/* services band */
.band{top:635px;height:176px;width:600px}
.band.business{left:0;background:var(--navy)}
.band.personal{left:600px;background:var(--green)}
.band-circle{width:112px;height:112px;border:3px solid var(--white);border-radius:50%;display:flex;align-items:center;justify-content:center}
.band-title{color:var(--white);font-family:"EB Garamond",Georgia,serif;font-style:italic;font-weight:600;font-size:25px}
.band-text{color:#e8eef7;font-size:11px;line-height:18px;width:305px}
.band-more{color:var(--white);font-size:10.5px;font-weight:700}

/* welcome */
.shadow-curve{left:40px;top:810px;width:1120px;height:20px;background:radial-gradient(ellipse at 50% 0,rgba(0,0,0,.18),rgba(0,0,0,0) 70%)}
.welcome-photo{left:162px;top:848px;width:341px;height:260px;border:5px solid #f3f3f3;box-shadow:0 0 3px rgba(0,0,0,.2);background:linear-gradient(120deg,#e9ecef,#cdd6df 50%,#f4f1ec)}
.welcome-title{left:533px;top:838px;font-family:"EB Garamond",Georgia,serif;font-style:italic;font-weight:600;font-size:29px;line-height:30px;color:#333}
.welcome-text{left:533px;top:908px;width:510px;font-size:10.6px;line-height:20px;color:#444}
.welcome-text p+p{margin-top:20px}

/* cards */
.grey-band{left:0;top:1148px;width:1200px;height:424px;background:linear-gradient(#e6e6e6,var(--grey-bg) 40%,#f6f6f6)}
.card{top:1196px;width:277px;height:331px;background:var(--white);border:1px solid #dadada;text-align:center}
.card-photo{height:148px}
.card-title{margin-top:20px;font-family:"EB Garamond",Georgia,serif;font-style:italic;font-weight:600;font-size:24px;color:var(--green-text)}
.card-text{margin:10px auto 0;width:240px;font-size:11px;line-height:19px;color:#444}
.btn-more{margin:18px auto 0;width:92px;height:30px;background:var(--navy);color:var(--white);font-size:10.5px;font-weight:600;display:flex;align-items:center;justify-content:center;gap:4px}

/* mission */
.mission-title{left:162px;top:1610px;font-family:"EB Garamond",Georgia,serif;font-style:italic;font-weight:600;font-size:20px;line-height:22px;color:var(--green-text)}
.mission-divider{left:393px;top:1612px;width:1px;height:46px;background:var(--line)}
.mission-text{left:421px;top:1614px;width:625px;font-size:10.8px;line-height:20px;color:#444}
.rule{left:162px;top:1688px;width:878px;height:1px;background:var(--line)}

/* agents */
.agents-title{left:162px;top:1706px;font-family:"EB Garamond",Georgia,serif;font-style:italic;font-weight:600;font-size:31px;color:#333}
.agent-info{left:162px;top:1752px;width:560px;font-size:10.6px;line-height:20px;color:#444}
.agent-info b{color:var(--green-text);font-weight:600}
.agent-meta{margin-top:12px;line-height:21px}
.agent-photo{left:735px;top:1716px;width:304px;height:203px;border:3px solid #f3f3f3;box-shadow:0 0 3px rgba(0,0,0,.2);background:linear-gradient(90deg,#c8d8e6,#eef3f7 55%,#b7c7d6)}

/* footer */
.footer{left:0;top:1962px;width:1200px;height:270px;background:linear-gradient(120deg,var(--navy-deep),var(--navy) 60%,#1c4583)}
.foot-title{top:1986px;font-family:"EB Garamond",Georgia,serif;font-style:italic;font-weight:600;font-size:25px;color:var(--white)}
.field{background:var(--white);height:37px;font-size:11px;font-style:italic;color:#888;padding:10px 8px}
.btn-submit{left:380px;top:2137px;width:92px;height:37px;background:var(--green);color:var(--white);font-size:12.5px;font-weight:700;display:flex;align-items:center;justify-content:center;gap:5px}
.map{left:513px;top:2030px;width:316px;height:144px;background:linear-gradient(135deg,#e9ecef,#d9e3e8 50%,#b8d3e8)}
.contact-list{left:875px;top:2030px;width:175px;font-size:11px;line-height:17px;color:#e7ecf5}
.contact-list li{list-style:none;display:flex;gap:9px;margin-bottom:4px}
.contact-list svg{flex:none;margin-top:3px}
.bottom-bar{left:0;top:2232px;width:1200px;height:58px;background:var(--green)}
.copyright{left:160px;top:2252px;font-size:11px;color:var(--white)}
.social{top:2247px;width:27px;height:27px;border:2px solid var(--white);border-radius:50%}
</style>
</head>
<body>
<div class="abs topline"></div>

<header>
  <div class="abs brand"><span class="brand-mark"></span>Harborline Insurance Group</div>
  <div class="abs top-contact" style="left:679px">
    <span class="icon-ring"><svg width="12" height="9" viewBox="0 0 12 9"><rect width="12" height="9" rx="1" fill="#2a7d3c"/><path d="M0.5 0.8L6 5l5.5-4.2" stroke="#fff" fill="none" stroke-width="1.2"/></svg></span>
    Email: info@company.Com
  </div>
  <div class="abs top-contact" style="left:885px">
    <span class="icon-ring"><svg width="12" height="12" viewBox="0 0 12 12"><path d="M2.5 1l2 2.3-1 1.4c.8 1.6 2 2.8 3.6 3.6l1.4-1 2.3 2-1 1.6C5 10.5 1.5 7 .9 2z" fill="#2a7d3c"/></svg></span>
    Phone: 000-000-0009
  </div>
  <nav>
    <span class="abs nav-item active" style="left:459px">HOME</span>
    <span class="abs nav-item" style="left:543px">OUR SERVICES</span>
    <span class="abs nav-item" style="left:677px">ABOUT US</span>
    <span class="abs nav-item" style="left:787px">CLIENT LIST</span>
    <span class="abs nav-item" style="left:904px">CONTACT US</span>
  </nav>
  <div class="abs search"><svg width="13" height="13" viewBox="0 0 13 13"><circle cx="5.3" cy="5.3" r="3.8" stroke="#fff" stroke-width="2" fill="none"/><path d="M8.2 8.2l3.5 3.5" stroke="#fff" stroke-width="2"/></svg></div>
</header>

<section class="abs hero" role="img" aria-label="Photo of a smiling family of four on a lawn in front of their house"></section>
<svg class="abs hero-arrow" style="left:40px" width="28" height="56" viewBox="0 0 28 56"><path d="M26 2L3 28l23 26" stroke="#fff" stroke-width="2" fill="none"/></svg>
<svg class="abs hero-arrow" style="left:1130px" width="28" height="56" viewBox="0 0 28 56"><path d="M2 2l23 26L2 54" stroke="#fff" stroke-width="2" fill="none"/></svg>
<h1 class="abs hero-title">Harborline<br>Insurance Group</h1>
<div class="abs btn-quote">GET A QUOTE NOW <svg width="8" height="12" viewBox="0 0 8 12"><path d="M1.5 1l5 5-5 5" stroke="#fff" stroke-width="2" fill="none"/></svg></div>

<section class="abs band business">
  <div class="abs band-circle" style="left:161px;top:31px">
    <svg width="56" height="50" viewBox="0 0 56 50" fill="#fff"><circle cx="28" cy="12" r="9"/><path d="M14 50c0-14 6-24 14-24s14 10 14 24z"/><circle cx="11" cy="17" r="6.5"/><path d="M0 44c0-10 4-17 11-17 3 0 5 1 6 3-3 4-5 9-5 14z"/><circle cx="45" cy="17" r="6.5"/><path d="M56 44c0-10-4-17-11-17-3 0-5 1-6 3 3 4 5 9 5 14z"/></svg>
  </div>
  <div class="abs band-title" style="left:292px;top:20px">Business Insurance</div>
  <p class="abs band-text" style="left:290px;top:63px">Sed ut perspiciatis unde omnis iste natus error sit volupt atem accusantium doloremque laudantium, totam rem aperiam, eaque ipsa quae ab illo inventore verita.</p>
  <div class="abs band-more" style="left:292px;top:132px">READ MORE »</div>
</section>
<section class="abs band personal">
  <div class="abs band-circle" style="left:33px;top:31px">
    <svg width="42" height="46" viewBox="0 0 42 46" fill="#fff"><circle cx="21" cy="12" r="11"/><path d="M0 46c0-14 9-21 21-21s21 7 21 21z"/></svg>
  </div>
  <div class="abs band-title" style="left:164px;top:20px">Personal Insurance</div>
  <p class="abs band-text" style="left:162px;top:63px">Sed ut perspiciatis unde omnis iste natus error sit volupt atem accusantium doloremque laudantium, totam rem aperiam, eaque ipsa quae ab illo inventore verita.</p>
  <div class="abs band-more" style="left:164px;top:132px">READ MORE »</div>
</section>

<div class="abs shadow-curve"></div>
<div class="abs welcome-photo" role="img" aria-label="Photo of a couple meeting with an insurance agent at a desk"></div>
<h2 class="abs welcome-title">Welcome to<br>Harborline Insurance Group</h2>
<div class="abs welcome-text">
  <p>Harborline Insurance Group has joined with regional &amp; national insurance companies to provide quality products and superior service. We take the time to discuss options and coverages, not to just sell insurance products. We strive to educate you in the decision making process to become an informed consumer. We specialize in commercial business &amp; personal insurance. We are committed to providing personal attention to all your insurance needs.</p>
  <p>At Harborline Insurance Group, we are independent insurance agents. As independent agents, we do not work for any one insurance company; we sell coverage from several different companies. This allows us to focus on providing you with the right amount of insurance and the right type of coverage for your unique needs.</p>
</div>

<div class="abs grey-band"></div>
<article class="abs card" style="left:162px">
  <div class="card-photo" role="img" aria-label="Photo of a couple shaking hands with a real estate agent outside a house" style="background:linear-gradient(120deg,#9aa3a8,#c9c3b8 50%,#7f8a7a)"></div>
  <h3 class="card-title">About Us</h3>
  <p class="card-text">Sed ut perspiciatis undlorere omnis isssitem accusantiunde omniremqdptatem acsaniunde omnireptatem accuiremqdptatem ac santi.</p>
  <div class="btn-more">READ MORE <svg width="6" height="9" viewBox="0 0 6 9"><path d="M1 1l3.5 3.5L1 8" stroke="#fff" stroke-width="1.6" fill="none"/></svg></div>
</article>
<article class="abs card" style="left:465px">
  <div class="card-photo" role="img" aria-label="Photo of hands signing a contract on a desk" style="background:linear-gradient(160deg,#5d6a7a,#b9c4cf 55%,#e6e9ec)"></div>
  <h3 class="card-title">Who We Are</h3>
  <p class="card-text">Sed ut perspiciatis undlorere omnis isssitem accusantiunde omniremqdptatem acsaniunde omnireptatem accuiremqdptatem ac santi.</p>
  <div class="btn-more">READ MORE <svg width="6" height="9" viewBox="0 0 6 9"><path d="M1 1l3.5 3.5L1 8" stroke="#fff" stroke-width="1.6" fill="none"/></svg></div>
</article>
<article class="abs card" style="left:761px">
  <div class="card-photo" role="img" aria-label="Photo of business people reviewing a document together" style="background:linear-gradient(110deg,#3a4250,#c9c1b7 50%,#565d68)"></div>
  <h3 class="card-title">What We Do</h3>
  <p class="card-text">Sed ut perspiciatis undlorere omnis isssitem accusantiunde omniremqdptatem acsaniunde omnireptatem accuiremqdptatem ac santi.</p>
  <div class="btn-more">READ MORE <svg width="6" height="9" viewBox="0 0 6 9"><path d="M1 1l3.5 3.5L1 8" stroke="#fff" stroke-width="1.6" fill="none"/></svg></div>
</article>

<h3 class="abs mission-title">Harborline Insurance<br>Group Mission Statement</h3>
<div class="abs mission-divider"></div>
<p class="abs mission-text">Harborline Insurance Group is committed to providing the best risk management solutions to fit each client's unique needs. This includes providing creative solutions as if we were seeking insurance for our own family.</p>
<div class="abs rule"></div>

<h2 class="abs agents-title">Our Agents</h2>
<div class="abs agent-info">
  <p><b>Daniel's Bio:</b> Sed ut perspiciatis unde omnis iste natus error sit voluptatem accusantium doloremque laudantium, totam rloem aperiam, eaque ipsainventore veritatis et quasi architecto beatae vitae dicta sunt explicaboemo enim ipsam voluptatem quia voluptassit aspernSed ut perspiciatis unde omnis iste natus error sit voluptatem accusantium doloremque laloiud antium, totam rem aperiam, eaque ipsainventore veritati.</p>
  <div class="agent-meta">
    <div><b>Education:</b> Seriam, eaque ipsainventore ver</div>
    <div><b>Insurance experience:</b> Speriam, eaque ipsainventore ver, eaque ipsainven</div>
    <div><b>Professional memberships:</b> Deriam, eaque ipsai periam,Waque ipsainvento</div>
  </div>
</div>
<div class="abs agent-photo" role="img" aria-label="Photo of an agent in a grey suit standing in an office"></div>

<footer>
  <div class="abs footer"></div>
  <h3 class="abs foot-title" style="left:162px">Contact form</h3>
  <h3 class="abs foot-title" style="left:513px">Map</h3>
  <h3 class="abs foot-title" style="left:875px">Contact Us</h3>

  <div class="abs field" style="left:162px;top:2030px;width:152px">Name:</div>
  <div class="abs field" style="left:319px;top:2030px;width:153px">Email:</div>
  <div class="abs field" style="left:162px;top:2072px;width:152px">Phone:</div>
  <div class="abs field" style="left:319px;top:2072px;width:153px">Service:</div>
  <div class="abs field" style="left:162px;top:2114px;width:310px;height:60px">Message:</div>
  <div class="abs btn-submit">SUBMIT <svg width="11" height="11" viewBox="0 0 11 11"><circle cx="5.5" cy="5.5" r="4.6" stroke="#fff" stroke-width="1.3" fill="none"/><path d="M4.5 3.3l2.2 2.2-2.2 2.2" stroke="#fff" stroke-width="1.3" fill="none"/></svg></div>

  <div class="abs map" role="img" aria-label="Street map showing the office location"></div>

  <ul class="abs contact-list">
    <li><svg width="8" height="11" viewBox="0 0 8 11"><path d="M4 0a4 4 0 0 0-4 4c0 3 4 7 4 7s4-4 4-7a4 4 0 0 0-4-4z" fill="#fff"/><circle cx="4" cy="4" r="1.4" fill="#173b72"/></svg><span>We are located in the Cedar Point Office Park in Orlando, Florida 1280 NW 14th Street, Suite 305 Orlando, FL 32801</span></li>
    <li><svg width="9" height="9" viewBox="0 0 12 12"><path d="M2.5 1l2 2.3-1 1.4c.8 1.6 2 2.8 3.6 3.6l1.4-1 2.3 2-1 1.6C5 10.5 1.5 7 .9 2z" fill="#fff"/></svg><span>Phone: (555)</span></li>
    <li><svg width="10" height="9" viewBox="0 0 10 9"><rect x="0" y="3" width="10" height="6" fill="#fff"/><rect x="2" y="0" width="6" height="3" fill="#fff"/></svg><span>Fax: (555) 014-2290</span></li>
  </ul>

  <div class="abs bottom-bar"></div>
  <p class="abs copyright">© 2016 HIG .All copyrights are reserved&nbsp; Term of Use, Privay Policy</p>
  <span class="abs social" style="left:923px"></span>
  <span class="abs social" style="left:952px"></span>
  <span class="abs social" style="left:981px"></span>
  <span class="abs social" style="left:1010px"></span>
</footer>
</body>
</html>
```